Exciting new aperitif brand needs a great label

Vel-Orin is a wonderful rich new premium-priced bitter aperitif, with a deep red colour, from a 100+ year old distillery (1890) near Turin in the Piedmont region of Italy. Inspired by Tessoni, it is perfectly formulated to elevate the classic Bravetti cocktail (and variations on it). It also goes perfectly in a Spritz or a long mixed drink with soda or tonic. The name Vel-Orin is derived from the French for 'peak' and the Italian word for 'love'.

The label, which should take inspiration from Tessoni, but be distinctively different, can incoporate any number of premium label embellishments (foil, embossing, textures etc) and should be no greater than 11cm (height) x 9cm (width) with any core imagery restricted to a width of c.7cm.

The attached mood board should act as inspiration and colour should largely be restricted to reds, blues, whites and perhaps orange. For completeness, the label should note that the ABV is 25% and the bottle size 70cl.

Target Market(s)

21-45yr olds - equal split female/male

Colors
0054AA
0677BA
7BADD7
CADEEF
E8F1F8
0094D4
00A9DD
6FCCEA
C7EBF8
E9F6FB
EE7325
F08F49
F5BC92
FAE3D3
FDF4ED
EB3D1F
EC4F4E
F09395
F8D3D4
FCEDEE

Requirements
Must have
• Great lettering design on the name Vel-Orin

```html
<!DOCTYPE html>
<html lang="en">
<head>
<meta charset="utf-8">
<title>Vel-Orin Aperitivo Label</title>
<link rel="stylesheet" href="https://fonts.googleapis.com/css2?family=Cinzel:wght@700&family=Crimson+Pro:wght@600&family=Great+Vibes&family=Pinyon+Script&display=swap">
<style>
  :root {
    --stage: #08080a;
    --paper: #d8e8f7;
    --panel: #dcebf8;
    --panel-deep: #c7ddf1;
    --navy: #0b3a78;
    --navy-deep: #072a5a;
    --navy-light: #1a5296;
    --gold: #f0a91e;
    --gold-light: #ffd86a;
    --gold-dark: #b97a0c;
    --flag-red: #d9261c;
    --white: #ffffff;
    --ink: #1a1a1a;
  }
  html, body {
    margin: 0;
    padding: 0;
    width: 1011px;
    height: 1200px;
    overflow: hidden;
    background: var(--stage);
  }
  .label-canvas {
    display: block;
    width: 1011px;
    height: 1200px;
  }
  .region-script { font-family: "Pinyon Script", cursive; }
  .brand-name { font-family: "Cinzel", serif; font-weight: 700; }
  .spec { font-family: "Crimson Pro", serif; font-weight: 600; fill: var(--ink); font-size: 33px; }
  .since { font-family: "Crimson Pro", serif; font-weight: 600; fill: var(--white); font-size: 26px; letter-spacing: 2px; }
  .style-script { font-family: "Great Vibes", cursive; }
  .origin { font-family: "Crimson Pro", serif; font-weight: 600; fill: var(--ink); font-size: 12px; letter-spacing: 2.4px; }
</style>
</head>
<body>
<svg class="label-canvas" viewBox="0 0 1011 1200" xmlns="http://www.w3.org/2000/svg">
  <defs>
    <linearGradient id="gold-foil" x1="0" y1="0" x2="0" y2="1">
      <stop offset="0" stop-color="var(--gold-light)"/>
      <stop offset="0.55" stop-color="var(--gold)"/>
      <stop offset="1" stop-color="var(--gold-dark)"/>
    </linearGradient>
    <linearGradient id="band-navy" x1="0" y1="0" x2="1" y2="0">
      <stop offset="0" stop-color="var(--navy-deep)"/>
      <stop offset="0.5" stop-color="var(--navy-light)"/>
      <stop offset="1" stop-color="var(--navy-deep)"/>
    </linearGradient>
    <linearGradient id="border-fill" x1="0" y1="0" x2="1" y2="1">
      <stop offset="0" stop-color="var(--navy)"/>
      <stop offset="0.5" stop-color="#2b5c92"/>
      <stop offset="1" stop-color="var(--navy)"/>
    </linearGradient>
    <radialGradient id="panel-fill" cx="0.5" cy="0.5" r="0.7">
      <stop offset="0" stop-color="var(--panel)"/>
      <stop offset="1" stop-color="var(--panel-deep)"/>
    </radialGradient>
    <path id="since-arc" d="M 372,514 A 134 134 0 0 0 640,514"/>
  </defs>

  <!-- label sheet -->
  <rect class="label-sheet" x="94" y="96" width="824" height="1007" fill="var(--paper)"/>

  <!-- frame -->
  <g class="frame">
    <rect x="129" y="130" width="756" height="933" fill="none" stroke="var(--gold)" stroke-width="3"/>
    <path class="frame-ornament" role="img" aria-label="Ornamental gold-and-blue floral border"
          fill-rule="evenodd" fill="url(#border-fill)"
          d="M134,135 H880 V1058 H134 Z M172,173 V1020 H842 V173 Z"/>
    <rect x="138" y="139" width="738" height="915" fill="none" stroke="var(--gold)" stroke-width="2"/>
    <rect x="168" y="169" width="678" height="855" fill="none" stroke="var(--gold)" stroke-width="2"/>
    <rect x="176" y="177" width="662" height="839" fill="none" stroke="var(--gold)" stroke-width="3"/>
  </g>

  <!-- inner panel -->
  <rect class="inner-panel" role="img" aria-label="Embossed interlaced knotwork background pattern"
        x="184" y="185" width="646" height="823" fill="url(#panel-fill)" stroke="var(--gold-dark)" stroke-width="1.5"/>

  <!-- regional flag -->
  <g class="region-flag">
    <rect x="449" y="208" width="113" height="78" fill="var(--navy)"/>
    <rect x="453" y="212" width="105" height="70" fill="var(--flag-red)"/>
    <rect x="496" y="212" width="19" height="70" fill="var(--white)"/>
    <rect x="453" y="238" width="105" height="18" fill="var(--white)"/>
  </g>

  <!-- region script -->
  <text class="region-script" x="498" y="388" text-anchor="middle" font-size="104"
        fill="url(#gold-foil)" stroke="var(--gold-dark)" stroke-width="0.8" textLength="340">Piedmont</text>

  <!-- name band -->
  <g class="name-band">
    <rect x="94" y="420" width="824" height="178" fill="url(#band-navy)"/>
    <rect x="94" y="432" width="824" height="5" fill="var(--gold)"/>
    <rect x="94" y="442" width="824" height="2" fill="var(--gold)"/>
    <rect x="94" y="576" width="824" height="2" fill="var(--gold)"/>
    <rect x="94" y="583" width="824" height="5" fill="var(--gold)"/>
  </g>

  <!-- since badge -->
  <g class="since-badge">
    <path d="M 382,598 A 150 150 0 0 0 630,598 Z" fill="var(--navy)" stroke="var(--gold)" stroke-width="5"/>
    <rect x="376" y="596" width="260" height="4" fill="var(--navy)"/>
    <text class="since"><textPath href="#since-arc" startOffset="50%" text-anchor="middle">Since 1890</textPath></text>
  </g>

  <!-- brand name -->
  <g class="brand-name" font-size="138" text-anchor="middle">
    <text x="506" y="553" textLength="646" lengthAdjust="spacingAndGlyphs" fill="var(--gold)" stroke="var(--gold)" stroke-width="10" stroke-linejoin="round">VEL-ORIN</text>
    <text x="506" y="553" textLength="646" lengthAdjust="spacingAndGlyphs" fill="var(--white)" stroke="var(--navy-deep)" stroke-width="3" stroke-linejoin="round" paint-order="stroke">VEL-ORIN</text>
  </g>

  <!-- specs -->
  <text class="spec" x="203" y="656">25% vol.</text>
  <text class="spec" x="813" y="656" text-anchor="end">700 ml.</text>

  <!-- style script -->
  <text class="style-script" x="530" y="858" text-anchor="middle" font-size="196"
        fill="url(#gold-foil)" stroke="var(--gold-dark)" stroke-width="1" textLength="540" lengthAdjust="spacingAndGlyphs">Aperitivo</text>
  <text class="style-script" x="630" y="906" text-anchor="middle" font-size="34"
        fill="var(--gold)" textLength="330" transform="rotate(-7 630 906)">premium-priced bitter</text>

  <!-- origin line -->
  <text class="origin" x="506" y="992" text-anchor="middle">PRODUCED BY ITALY</text>
</svg>
</body>
</html>
```